Counseling Practice Business Card

I need a professional looking business card incorporating my new logo that was just completed. Card needs to incorporate my name and title, description of my specialty, my address, my phone number, my fax number, my email and my website URL. I need to be able to choose design on/with different paper colors and textures.
I do not have a lot of business card ideas so I am open to anything but I want bold,sharp, clear card without additional designs other than my logo (see attached file info). I am open to different color backgrounds or paper colors including black. I do not like traditional brackets around area codes in phone number or dashes between numbers in phone number. Am open to other ways of presenting including periods between numbers as appropriate. I do not know enough to know what I like yet but I want card to coordinate and work together with my logo. My practice emphasizes natural mental health interventions so any use of color (with background paper color or the blue and green in my logo) that elicits nature is nice. In addition to black, any natural brown or wood looking background might be desirable also. Most of the offerings so far look very similar and boring.

Target Market(s)

Potential therapy clients and other professionals

Contact Information for Business Card

Card information:
Gerald M. Whitcombe, Ph.D.
Licensed Clinical Psychologist
Integrative Health Coach
4812 Marlowe Ridge Blvd SE
Suite 310
Duluth, GA 30096
(770) 415-2983 phone
(770) 581-4096 fax
drgeraldwhitcombe@quillmarsh.net
brightfernwellness.net

Font styles to use
Serif
Sans Serif
Other font styles liked:
• anything that you think looks crisp, clear and easily readable

Requirements
Must have
• Any color used should coordinate with my logo design (see attached files).
• Card should be printed horizontally so top and bottom are longest sides of rectangle.
• Background color or paper color should complement and highlight logo. Do not like a white background. black, grey, brown or any color my logo would blend well with.
Nice to have
• I would like designer to utilize color to highlight letters/name or phone-fax-web symbols.
• Bottom edge of card could be highlighted if appropriate to an idea.
Should not have
• I would NOT want the card to have a pure white background at all.
• No clear cards.
• Cards should be oriented with long sides on bottom and top, NOT sides. DO NOT LIKE THIS THIN TALL ORIENTATION.

```html
<!DOCTYPE html>
<html lang="en">
<head>
<meta charset="UTF-8">
<title>Brightfern Wellness – Business Card</title>
<link href="https://fonts.googleapis.com/css2?family=Roboto:wght@400;500;700&display=swap" rel="stylesheet">
<style>
  :root {
    --stage: #e4e6e9;
    --card-grey: #d9dde1;
    --card-grey-light: #e6e9ec;
    --card-grey-edge: #c9ced3;
    --brand-blue: #1f6fb8;
    --brand-blue-deep: #17609f;
    --brand-blue-light: #2f86cc;
    --text-dark: #33373b;
    --logo-light: #d9dde2;
  }
  * { box-sizing: border-box; margin: 0; padding: 0; }
  html, body { width: 1200px; height: 900px; overflow: hidden; }
  body {
    background: var(--stage);
    font-family: "Roboto", Arial, sans-serif;
    display: flex;
    flex-direction: column;
    align-items: center;
    justify-content: center;
    gap: 56px;
  }
  .card {
    width: 600px;
    height: 343px;
    border-radius: 18px;
    position: relative;
    overflow: hidden;
    box-shadow: 0 6px 18px rgba(0,0,0,0.18);
  }
  /* Front */
  .card-front {
    background: radial-gradient(circle at 62% 72%, var(--card-grey-light) 0%, var(--card-grey) 45%, var(--card-grey-edge) 100%);
  }
  .contact-block {
    position: absolute;
    left: 40px;
    top: 50px;
    width: 330px;
    color: var(--text-dark);
    font-size: 15px;
    line-height: 1.34;
  }
  .person-name {
    color: var(--brand-blue);
    font-weight: 700;
    font-size: 21px;
    margin-bottom: 4px;
  }
  .person-title, .address-line { font-weight: 500; }
  .address { margin-top: 8px; }
  .contact-list { list-style: none; margin-top: 8px; }
  .contact-list li { display: flex; align-items: center; gap: 8px; font-weight: 500; white-space: nowrap; }
  .contact-icon { width: 12px; height: 12px; fill: var(--brand-blue); flex: none; }
  .web-accent { color: var(--brand-blue); }
  .brand-front {
    position: absolute;
    right: 44px;
    top: 140px;
    display: flex;
    align-items: center;
    gap: 12px;
    color: var(--brand-blue);
    font-weight: 700;
    font-size: 32px;
    line-height: 1.05;
  }
  .brand-dot { width: 18px; height: 18px; border-radius: 50%; background: var(--brand-blue); flex: none; }
  /* Back */
  .card-back {
    background: linear-gradient(135deg, var(--brand-blue-light) 0%, var(--brand-blue) 50%, var(--brand-blue-deep) 100%);
  }
  .world-map {
    position: absolute;
    inset: 0;
    background: radial-gradient(ellipse at 55% 45%, rgba(255,255,255,0.10) 0%, rgba(255,255,255,0.04) 55%, rgba(255,255,255,0) 80%);
  }
  .brand-back {
    position: absolute;
    left: 0; right: 0;
    top: 118px;
    text-align: center;
    color: var(--logo-light);
    font-weight: 700;
    font-size: 44px;
  }
  .back-url {
    position: absolute;
    left: 0; right: 0;
    top: 210px;
    text-align: center;
    color: var(--logo-light);
    font-weight: 500;
    font-size: 17px;
  }
</style>
</head>
<body>
  <section class="card card-front">
    <div class="contact-block">
      <div class="person-name">Gerald M. Whitcombe, Ph.D.</div>
      <div class="person-title">Licensed Clinical Psychologist</div>
      <div class="person-title">Integrative Health Coach</div>
      <div class="address">
        <div class="address-line">4812 Marlowe Ridge Blvd SE</div>
        <div class="address-line">Suite 310 Duluth, GA 30096</div>
      </div>
      <ul class="contact-list">
        <li>
          <svg class="contact-icon" viewBox="0 0 24 24"><path d="M6.6 10.8a15 15 0 0 0 6.6 6.6l2.2-2.2a1 1 0 0 1 1-.25 11.4 11.4 0 0 0 3.6.57 1 1 0 0 1 1 1V20a1 1 0 0 1-1 1A17 17 0 0 1 3 4a1 1 0 0 1 1-1h3.5a1 1 0 0 1 1 1c0 1.25.2 2.45.57 3.57a1 1 0 0 1-.25 1z"/></svg>
          770.415.2983
        </li>
        <li>
          <svg class="contact-icon" viewBox="0 0 24 24"><path d="M7 2h10v6H7zM3 9h18v10h-4v3H7v-3H3zm6 7v4h6v-4z"/></svg>
          770.581.4096
        </li>
        <li>
          <svg class="contact-icon" viewBox="0 0 24 24"><path d="M2 5h20v14H2zm2 2v.5l8 5 8-5V7zm0 2.8V17h16V9.8l-8 5z"/></svg>
          drgeraldwhitcombe@quillmarsh.net
        </li>
        <li>
          <svg class="contact-icon" viewBox="0 0 24 24"><circle cx="12" cy="12" r="10"/></svg>
          <span>www.<span class="web-accent">brightfernwellness</span>.net</span>
        </li>
      </ul>
    </div>
    <div class="brand-front">
      <span class="brand-dot"></span>
      <span>Brightfern<br>Wellness</span>
    </div>
  </section>

  <section class="card card-back">
    <div class="world-map" role="img" aria-label="Faint world map pattern across the card"></div>
    <div class="brand-back">Brightfern Wellness</div>
    <div class="back-url">www.brightfernwellness.net</div>
  </section>
</body>
</html>
```